Whitcombe Business Card Design

The name of the business is Dario Whitcombe, CPA LLC
The service that we offer is Accounting, Tax & Consulting Services. I need it to have the following items:
Dario Whitcombe, Principal
Phone Number
Email Address
Physical Address

I have attached the company logo, one in black and one in white. Please provide a design in black background and the other in white background. Please include "Accounting, Tax & Consulting Services". I want the business card to be clean and very professional.

```html
<!DOCTYPE html>
<html lang="en">
<head>
<meta charset="utf-8">
<title>Dario Whitcombe, CPA LLC — Business Card</title>
<link rel="stylesheet" href="https://fonts.googleapis.com/css2?family=Open+Sans:wght@400;600&family=Montserrat:wght@400;500&display=swap">
<style>
  :root {
    --backdrop: #1c1c1c;
    --card-light: #e6e7e8;
    --card-dark: #3a3a3c;
    --ink: #3d3d3f;
    --accent: #9b1b1f;
    --ink-light: #f2f2f2;
  }
  * { margin: 0; padding: 0; box-sizing: border-box; }
  html, body { width: 1200px; height: 1200px; overflow: hidden; }
  body {
    background: var(--backdrop);
    position: relative;
    font-family: "Open Sans", Arial, sans-serif;
  }
  .card {
    position: absolute;
    width: 744px;
    height: 429px;
    left: 251px;
  }
  .card--front { top: 172px; background: var(--card-light); color: var(--ink); }
  .card--back { top: 646px; background: var(--card-dark); color: var(--ink-light); }

  /* front */
  .brand-mark {
    position: absolute;
    left: 112px; top: 196px;
    display: flex; align-items: center; gap: 10px;
    font-family: "Montserrat", Arial, sans-serif;
    font-weight: 500;
    font-size: 26px;
    color: var(--ink);
  }
  .brand-mark__square { width: 16px; height: 16px; background: var(--accent); }
  .divider {
    position: absolute; left: 363px; top: 122px;
    width: 2px; height: 187px;
    background: linear-gradient(to bottom, transparent, var(--accent) 12%, var(--accent) 88%, transparent);
  }
  .details { position: absolute; left: 438px; top: 118px; }
  .details__name {
    font-family: "Montserrat", Arial, sans-serif;
    font-size: 22px; font-weight: 400; letter-spacing: 0.5px;
    text-transform: uppercase; color: var(--ink);
  }
  .details__name-first { color: var(--accent); }
  .details__role { font-size: 15px; margin-top: 2px; }
  .details__address { color: var(--accent); font-size: 15px; line-height: 25px; margin-top: 18px; }
  .contact { list-style: none; margin-top: 14px; font-size: 15px; }
  .contact li { display: flex; align-items: center; gap: 10px; height: 24.5px; }
  .contact svg { width: 12px; height: 12px; fill: var(--accent); }

  /* back */
  .lockup {
    position: absolute; left: 114px; top: 170px;
    display: flex; align-items: center; gap: 16px;
  }
  .lockup__square { width: 40px; height: 40px; background: var(--ink-light); }
  .lockup__name {
    font-family: "Montserrat", Arial, sans-serif;
    font-size: 29px; font-weight: 400; letter-spacing: 0.5px;
    text-transform: uppercase; line-height: 1;
  }
  .lockup__title {
    font-family: "Montserrat", Arial, sans-serif;
    font-size: 18.5px; font-weight: 500; letter-spacing: 2.6px;
    text-transform: uppercase; margin-top: 8px;
  }
  .services {
    position: absolute; left: 0; right: 0; top: 372px;
    text-align: center; font-size: 27px; font-weight: 400;
  }
</style>
</head>
<body>
  <section class="card card--front" aria-label="Business card, front">
    <div class="brand-mark"><span class="brand-mark__square"></span>Whitcombe</div>
    <div class="divider"></div>
    <div class="details">
      <h1 class="details__name"><span class="details__name-first">Dario</span> Whitcombe</h1>
      <p class="details__role">Principal</p>
      <p class="details__address">Po box 5830 harlow<br>kelvin, ab tr-4k7</p>
      <ul class="contact">
        <li><svg viewBox="0 0 24 24" aria-hidden="true"><path d="M6.6 10.8a15.1 15.1 0 0 0 6.6 6.6l2.2-2.2c.3-.3.7-.4 1-.2 1.1.4 2.3.6 3.6.6.6 0 1 .4 1 1V20c0 .6-.4 1-1 1A17 17 0 0 1 3 4c0-.6.4-1 1-1h3.5c.6 0 1 .4 1 1 0 1.3.2 2.5.6 3.6.1.3 0 .7-.2 1z"/></svg>415 (0) 552 804 117</li>
        <li><svg viewBox="0 0 24 24" aria-hidden="true"><path d="M2 5h20v14H2z M2 5l10 8 10-8" /></svg>hello@whitcombecpa.com</li>
        <li><svg viewBox="0 0 24 24" aria-hidden="true"><circle cx="12" cy="12" r="10"/></svg>www.whitcombecpa.com</li>
      </ul>
    </div>
  </section>

  <section class="card card--back" aria-label="Business card, back">
    <div class="lockup">
      <span class="lockup__square"></span>
      <div>
        <p class="lockup__name">Dario Whitcombe, CPA LLC</p>
        <p class="lockup__title">Certified Public Accountant</p>
      </div>
    </div>
    <p class="services">Accounting, Tax &amp; Consulting Services</p>
  </section>
</body>
</html>
```